Antibacterial Hand Wash Squeeze Tube Label

We're looking for a contemporary label design for a new Antibacterial Hand Wash for an 8oz squeeze tube. The new consumer brand will be sold to consumers in major US retail stores & online. The moisturizing hand wash contains Aloe Vera, vitamin E, and other natural ingredients so the design should include the color green. Real photos are very effective on packaging, so a picture of Aloe Vera or possibly two hands washing would help draw consumers' attention to the tube on the retail shelf. The front label may wrap around the sides. Rear must be left mostly blank
Target Market(s)
US Consumers - retail stores & online
Industry/Entity Type
Consumer

```html
<!DOCTYPE html>
<html lang="en">
<head>
<meta charset="utf-8">
<title>Hand Wash Tube Label</title>
<link href="https://fonts.googleapis.com/css2?family=Montserrat:wght@400;500;800&display=swap" rel="stylesheet">
<style>
  :root {
    --page-bg: #ffffff;
    --label-bg: #ffffff;
    --band-top: #07943f;
    --band-mid: #5fbc5a;
    --band-bottom: #e2f0d9;
    --brand-green: #139447;
    --aloe-light: #8fdc6a;
    --aloe-deep: #3fae33;
    --skin: #ecc9b4;
    --ink: #111111;
    --white: #ffffff;
  }
  * { margin: 0; padding: 0; box-sizing: border-box; }
  html, body {
    width: 1200px;
    height: 752px;
    overflow: hidden;
    background: var(--page-bg);
  }
  .label {
    position: absolute;
    left: 289px;
    top: 26px;
    width: 622px;
    height: 700px;
    background: var(--label-bg);
    box-shadow: 0 0 28px rgba(0, 0, 0, 0.08);
    font-family: "Montserrat", sans-serif;
  }
  .label__band {
    position: absolute;
    left: 39px;
    top: 0;
    width: 100px;
    height: 100%;
    background: linear-gradient(to bottom, var(--band-top) 0%, var(--band-mid) 50%, var(--band-bottom) 100%);
  }
  .label__photo {
    position: absolute;
    left: 61px;
    top: 237px;
    width: 400px;
    height: 390px;
    z-index: 1;
  }
  .vertical-text {
    position: absolute;
    z-index: 2;
    writing-mode: vertical-rl;
    transform: rotate(180deg);
    white-space: nowrap;
    color: var(--white);
    line-height: 1;
  }
  .label__tagline {
    left: 52px;
    top: 152px;
    height: 344px;
    font-size: 17.5px;
    font-weight: 400;
    letter-spacing: 0.2px;
    text-align: left;
  }
  .label__title {
    left: 80px;
    top: 150px;
    height: 345px;
    font-size: 53px;
    font-weight: 800;
    letter-spacing: 1px;
  }
  .label__benefits {
    position: absolute;
    z-index: 2;
    left: 156px;
    top: 255px;
    list-style: none;
    color: var(--brand-green);
    font-size: 14px;
    font-weight: 500;
    line-height: 17px;
    letter-spacing: 0.3px;
  }
  .label__benefits li::before { content: "+ "; }
  .label__benefits .indent { padding-left: 6px; }
  .label__benefits .indent::before { content: ""; }
  .label__size {
    position: absolute;
    z-index: 2;
    left: 246px;
    top: 623px;
    color: var(--ink);
    font-size: 15px;
    font-weight: 500;
  }
</style>
</head>
<body>
  <main class="label">
    <div class="label__band"></div>

    <svg class="label__photo" viewBox="0 0 400 390" role="img" aria-label="Photo of sliced aloe vera leaves stacked with fresh stems, above a pair of soapy hands being washed">
      <defs>
        <radialGradient id="aloe-tone" cx="0.62" cy="0.45" r="0.55">
          <stop offset="0" stop-color="var(--aloe-light)"/>
          <stop offset="0.7" stop-color="var(--aloe-deep)" stop-opacity="0.55"/>
          <stop offset="1" stop-color="var(--aloe-deep)" stop-opacity="0"/>
        </radialGradient>
        <radialGradient id="hand-tone" cx="0.35" cy="0.8" r="0.4">
          <stop offset="0" stop-color="var(--skin)"/>
          <stop offset="1" stop-color="var(--skin)" stop-opacity="0"/>
        </radialGradient>
      </defs>
      <rect width="400" height="390" fill="url(#aloe-tone)"/>
      <rect width="400" height="390" fill="url(#hand-tone)"/>
    </svg>

    <div class="vertical-text label__tagline">ANTIBACTERIAL &amp; MOISTURIZING</div>
    <div class="vertical-text label__title">HAND WASH</div>

    <ul class="label__benefits">
      <li>ALOE VERA</li>
      <li>VITAMIN E</li>
      <li>OTHER NATURAL</li>
      <li class="indent">INGREDIENTS</li>
    </ul>

    <div class="label__size">8 oz</div>
  </main>
</body>
</html>
```